Tradlo - Forex Signal Services Moments Matter Most. Reshape your path.

I need an attractive eye catching web design that is azure friendly. I currently have a web programmer working on the backend of my website. Now I need a professional design to attract and retain customers. This site needs to be mobile friendly.

Tradlo is a highly reputable, trustworthy and professional site that offers forex signals to traders in all parts of the globe. With accurate and reliable forex signals, traders can not only make money but also boost their profits.

At Tradlo, we want our clients to have complete faith on us and our services! We also do not want our users to lead a simple and monotonous life. Instead our goal is to help them create an extra source of steady income. However, this is possible only when our clients resolve to change their lives for the better. They need to change their mindset and most importantly develop a positive frame of mind. That’s exactly why at Tradlo, we provide our clients with innumerable personal development tools and resources that’ll aid them in changing all the aspects of their lives. We want our traders to feel inspired and educate them in the right way!

Colors are flexible.

I do like the simplicity of www.brightmarkvo.example.
I do want a design more professional in appearance and not everything on page one.

I have not been able to decide on a logo. There is one of lower quality as I have not paid for it yet but I will if you decide it's the best for my business I will. Or should one feel that they have a better idea for a logo, I will pay for it if i like it.

I have included some of the content of my site so you can get a feel for where I am coming from.
(Please note that this content is still in the editing process)
Updates

Project Deadline Extended Reason: My content was not complete nor finalization of the final logo. We will allow a few more days for designers to modify the website.Thank you for your patience and understanding. Added Tuesday, January 24, 2017

Target Market(s)

I work with Forex Traders, Investors wanting to control their own portfolios, and remote nomads/mellienials

Coding

Coded - Design and coding required

Number of Pages Required

5+ page

Requirements
Must have
• I must have a professional clean look. I want the site to be interactive and eye catching. I want my audience hooked within seconds of opening it. It has to have all important information first. Photos must be legit and not spammy. I work as a representative in the financial market. I want my site to reflect that I stand by my product and reputation means everything to me. This site has to be engaging.
• Sorry, I should have included this earlier of what I will all need on this site.
• I'll have about Tradlo (my company, what we stand for, who we work with, my strategy, etc....
• about me (why i started this company, who I am)
• Performance (graphs and recent posts of signals)
• Membership (how to sign up)
• Terms of service/legal/disclaimers
• FAQS
• Personal Development Resources
• Forex Education Resources
Nice to have
• Quick links to bounce around the site faster.
Should not have
• I do not want over the top white collar conservative.

```html
<!DOCTYPE html>
<html lang="en">
<head>
<meta charset="utf-8">
<title>Tradlo - Forex Signal Services</title>
<link rel="stylesheet" href="https://fonts.googleapis.com/css2?family=Roboto:wght@400;500;700&family=Open+Sans:ital,wght@0,400;0,600;0,700;1,600&display=swap">
<style>
:root{
  --orange:#f07c22;
  --orange-dark:#e06a12;
  --ink:#222;
  --text:#444;
  --muted:#777;
  --line:#ddd;
  --gray-bg:#efefef;
  --white:#fff;
  --night:#0e1622;
}
*{box-sizing:border-box;margin:0;padding:0}
html,body{width:1200px;height:3789px;overflow:hidden;background:var(--white)}
body{font-family:"Open Sans",Arial,sans-serif;color:var(--text);font-size:14px}
section,header,footer{position:relative;width:1200px;overflow:hidden}
.abs{position:absolute}
.title{font-family:"Roboto",Arial,sans-serif;font-weight:500;text-align:center;width:100%;left:0}
.bar{display:block;width:60px;height:3px;background:var(--orange);margin:14px auto 0}

/* header */
.site-header{height:139px;border-bottom:1px solid var(--line);background:var(--white)}
.brand{left:126px;top:38px;display:flex;align-items:center;gap:12px}
.brand-dot{width:34px;height:34px;border-radius:50%;background:var(--orange)}
.brand-name{font-family:"Roboto",sans-serif;font-weight:500;font-size:34px;color:var(--ink)}
.topbar{top:24px;right:101px;display:flex;align-items:center;gap:14px;font-family:"Roboto",sans-serif;font-size:17px;color:var(--ink)}
.topbar .ico{width:32px;height:32px;border-radius:50%;display:flex;align-items:center;justify-content:center}
.topbar .mail .ico{background:var(--orange)}
.topbar .tel .ico{background:#555}
.topbar .item{display:flex;align-items:center;gap:8px;margin-right:20px}
.socials{display:flex;gap:6px}
.socials span{width:22px;height:22px;background:#8a8a8a;display:block}
.nav{top:90px;left:467px;display:flex;font-family:"Roboto",sans-serif;font-weight:500;font-size:15px;color:var(--ink)}
.nav a{color:inherit;text-decoration:none;padding-bottom:10px;margin-right:46px}
.nav a.active{color:var(--orange);border-bottom:2px solid var(--orange)}
.nav a:last-child{margin-right:0}

/* hero */
.hero{height:513px;background:linear-gradient(90deg,#eeeeee 0%,#e4e4e4 55%,#d6d6d6 100%)}
.hero h1{left:99px;top:96px;font-family:"Roboto",sans-serif;font-weight:500;font-size:38px;color:var(--ink);white-space:nowrap;z-index:2}
.hero h1 em{font-style:normal;color:var(--orange)}
.hero h2{left:99px;top:186px;font-family:"Roboto",sans-serif;font-weight:700;font-size:22px;color:var(--ink)}
.hero p{left:99px;top:232px;width:470px;font-size:15px;line-height:24px;color:var(--ink)}
.btn-outline{display:inline-flex;align-items:center;justify-content:center;border:2px solid var(--ink);background:var(--white);color:var(--ink);font-family:"Roboto",sans-serif;font-weight:500;font-size:15px}
.hero .btn-outline{left:99px;top:308px;width:123px;height:48px}
.dots{left:101px;top:392px;display:flex;gap:6px}
.dots span{width:14px;height:14px;border-radius:50%;border:2px solid #777;background:var(--white)}
.dots span.on{background:var(--orange);border-color:var(--orange)}
.hero-visual{left:745px;top:106px;width:354px;height:260px;border-radius:6px;background:linear-gradient(160deg,#1d2a3c 0%,#24456e 55%,#1a2432 100%);box-shadow:0 0 0 10px #222}

/* welcome */
.welcome{height:422px;background:var(--white)}
.welcome .title{top:60px;font-size:34px;color:var(--ink)}
.welcome .title em{font-style:normal;color:var(--orange)}
.welcome .lead{left:164px;top:156px;width:872px;text-align:center;font-size:15px;line-height:26px}
.welcome .accent{left:164px;top:226px;width:872px;text-align:center;font-size:16px;line-height:28px;color:var(--orange);font-weight:600}
.welcome .actions{left:0;top:315px;width:100%;display:flex;justify-content:center;gap:14px}
.btn-fill{display:inline-flex;align-items:center;justify-content:center;background:var(--orange);color:var(--white);font-family:"Roboto",sans-serif;font-weight:500;font-size:15px}
.welcome .btn-fill,.welcome .btn-outline{width:112px;height:44px}

/* services */
.services{height:497px;background:var(--gray-bg)}
.services .title{top:50px;font-size:32px;color:var(--orange)}
.card{top:156px;width:283px;height:281px;background:var(--white);box-shadow:0 1px 6px rgba(0,0,0,.12);text-align:center}
.card svg{margin-top:44px}
.card h3{margin-top:24px;font-family:"Roboto",sans-serif;font-weight:500;font-size:19px;color:var(--orange)}
.card p{margin:18px auto 0;width:220px;font-size:13.5px;line-height:23px;color:var(--text)}

/* strategy */
.strategy{height:475px;background:linear-gradient(180deg,#f3882f 0%,var(--orange) 100%)}
.strategy .title{top:50px;font-size:32px;color:var(--white)}
.strategy .bar{background:var(--white)}
.strategy .lead{left:126px;top:150px;width:948px;text-align:center;color:var(--white);font-size:15px;line-height:28px}
.strategy .box{left:101px;top:238px;width:998px;height:204px;border:1px solid rgba(255,255,255,.7);background:rgba(255,255,255,.14);display:flex;align-items:center;padding:0 36px}
.strategy .box p{color:var(--white);font-weight:700;font-size:14px;line-height:28px;text-align:center}

/* why us */
.why{height:460px;background:var(--white)}
.why-visual{left:114px;top:76px;width:328px;height:303px;background:linear-gradient(180deg,#f4f4f4 0%,#dcdcdc 100%);border-radius:6px}
.why h2{left:505px;top:60px;font-family:"Roboto",sans-serif;font-weight:500;font-size:34px;color:var(--ink)}
.why .bar{position:absolute;left:505px;top:110px;margin:0}
.why .lead{left:505px;top:124px;width:600px;font-size:14.5px;line-height:25px}
.checks{left:505px;top:190px;list-style:none}
.checks li{display:flex;align-items:center;gap:14px;height:36px;font-size:14.5px;font-weight:600;color:var(--ink)}

/* faq */
.faq{height:432px;background:var(--gray-bg)}
.faq .title{top:42px;font-size:32px;color:var(--orange)}
.q{left:99px;width:474px;height:45px;border:1px solid var(--orange);border-radius:23px;background:var(--white);color:var(--orange);font-size:15px;display:flex;align-items:center;justify-content:space-between;padding:0 22px}
.q.open{background:var(--orange);color:var(--white);border-radius:23px 0 0 23px}
.q.open::after{content:"";position:absolute;right:-26px;top:0;border-left:26px solid var(--orange);border-top:22.5px solid transparent;border-bottom:22.5px solid transparent}
.answer{left:619px;top:146px;width:480px}
.answer h3{font-family:"Roboto",sans-serif;font-weight:500;font-size:21px;color:var(--orange)}
.answer ul{list-style:none;margin-top:14px}
.answer li{display:flex;align-items:center;gap:12px;color:var(--orange);font-size:14.5px;line-height:28px}
.answer li span{width:14px;height:14px;border:2px solid var(--orange);border-radius:50%;flex:none}
.answer p{margin-top:20px;font-size:14.5px;line-height:25px;color:var(--text)}

/* investors */
.investors{height:376px;background:linear-gradient(180deg,#141d29 0%,var(--night) 60%,#0a0f16 100%)}
.investors .title{top:60px;font-size:32px;color:var(--white)}
.investors .lead{left:101px;top:130px;width:998px;text-align:center;color:var(--white);font-size:15.5px;line-height:30px}
.investors .quote{left:0;top:272px;width:100%;text-align:center;color:var(--white);font-style:italic;font-weight:600;font-size:19px}

/* contact */
.contact{height:399px;background:#f4f4f4}
.contact h2{left:99px;top:50px;font-family:"Roboto",sans-serif;font-weight:500;font-size:24px;color:var(--orange)}
.contact h2::after{content:"";display:block;width:50px;height:2px;background:var(--orange);margin-top:8px}
.info{left:99px;display:flex;align-items:center;gap:26px;font-size:16px;color:var(--ink);line-height:24px}
.info .ico{width:46px;height:46px;border-radius:50%;border:2px solid var(--orange);display:flex;align-items:center;justify-content:center;flex:none}
.info .ico.solid{background:var(--orange)}
.contact .form-title{left:485px;top:56px;font-size:16px;font-weight:600;color:var(--ink)}
.field{width:288px;height:38px;border:1px solid #555;background:var(--white);font-size:13.5px;color:var(--muted);padding:0 12px;display:flex;align-items:center}
.field.msg{width:614px;height:86px;align-items:flex-start;padding-top:9px}
.contact .btn-fill{left:485px;top:318px;width:116px;height:38px;font-size:14px}

/* footer */
.site-footer{height:76px;background:#f4f4f4;border-top:1px solid var(--line)}
.site-footer p{left:99px;top:28px;font-size:13.5px;color:var(--ink)}
.foot-social{right:101px;top:18px;display:flex;gap:12px}
.foot-social span{width:36px;height:36px;border-radius:50%;border:2px solid #333;display:block}
</style>
</head>
<body>

<header class="site-header">
  <div class="abs brand"><span class="brand-dot"></span><span class="brand-name">Tradlo</span></div>
  <div class="abs topbar">
    <div class="item mail"><span class="ico"><svg width="16" height="12" viewBox="0 0 16 12"><rect x="1" y="1" width="14" height="10" fill="none" stroke="#fff" stroke-width="1.6"/><path d="M1 1l7 6 7-6" fill="none" stroke="#fff" stroke-width="1.6"/></svg></span>info@tradlo.example</div>
    <div class="item tel"><span class="ico"><svg width="14" height="14" viewBox="0 0 24 24"><path d="M6.6 10.8a15 15 0 0 0 6.6 6.6l2.2-2.2c.3-.3.7-.4 1-.2 1.1.4 2.3.6 3.6.6.6 0 1 .4 1 1V20c0 .6-.4 1-1 1C10.6 21 3 13.4 3 4c0-.6.4-1 1-1h3.5c.6 0 1 .4 1 1 0 1.3.2 2.5.6 3.6.1.3 0 .7-.2 1z" fill="#fff"/></svg></span>180 555 0142</div>
    <div class="socials"><span></span><span></span><span></span><span></span><span></span></div>
  </div>
  <nav class="abs nav">
    <a class="active">HOME</a><a>SERVICES</a><a>OUR STRATEGY</a><a>WHY US</a><a>FAQ</a><a>CONTACT US</a>
  </nav>
</header>

<section class="hero">
  <h1 class="abs">WELCOME TO <em>TRADLO.EXAMPLE!</em></h1>
  <h2 class="abs">MOMENTS MATTER MOST. RESHAPE YOUR PATH</h2>
  <p class="abs">We use proven strategies to help traders in succeeding in the forex market.</p>
  <a class="abs btn-outline">Read More</a>
  <div class="abs dots"><span class="on"></span><span></span><span></span><span></span><span></span></div>
  <div class="abs hero-visual" role="img" aria-label="Trader standing before a screen showing sell and buy arrows"></div>
</section>

<section class="welcome">
  <h2 class="abs title">Welcome To <em>Tradlo</em><span class="bar"></span></h2>
  <p class="abs lead">We use proven strategies to help traders in succeeding in the forex market. Our forex experts provide high-probability, professional and consistent forex signals and charts that help traders in maximizing their profits and eliminating losses.</p>
  <p class="abs accent">Try our free Currency Education service to find out what differentiates us from our competitors and how we can aid you in becoming a professional trader!</p>
  <div class="abs actions"><a class="btn-fill">Read More</a><a class="btn-outline">Contact Us</a></div>
</section>

<section class="services">
  <h2 class="abs title">Forex Signal Services</h2>
  <div class="abs card" style="left:124px">
    <svg width="64" height="64" viewBox="0 0 64 64"><rect x="22" y="6" width="34" height="46" fill="none" stroke="#f07c22" stroke-width="3"/><path d="M30 18h18M30 26h18M30 34h12" stroke="#f07c22" stroke-width="3"/><circle cx="20" cy="40" r="11" fill="#fff" stroke="#444" stroke-width="3.5"/><path d="M12 48L4 56" stroke="#444" stroke-width="5" stroke-linecap="round"/></svg>
    <h3>Foreign Exchange</h3>
    <p>We provide marketing, consumer and business insights through the use of market research.</p>
  </div>
  <div class="abs card" style="left:460px">
    <svg width="64" height="64" viewBox="0 0 64 64"><rect x="10" y="8" width="46" height="36" fill="none" stroke="#f07c22" stroke-width="3"/><path d="M16 36l10-10 8 6 14-16" fill="none" stroke="#f07c22" stroke-width="3"/><path d="M4 50l10-6 10 4 8 8" fill="none" stroke="#444" stroke-width="4" stroke-linecap="round"/></svg>
    <h3>Trading Services</h3>
    <p>We provide marketing, consumer and business insights through the use of market research.</p>
  </div>
  <div class="abs card" style="left:793px">
    <svg width="64" height="64" viewBox="0 0 64 64"><path d="M10 28l28-16v36L10 36z" fill="#f07c22"/><rect x="4" y="26" width="8" height="12" fill="#444"/><path d="M16 38l4 14h6l-3-13" fill="#444"/><path d="M46 18l8-6M48 30h10M46 42l8 6" stroke="#444" stroke-width="3" stroke-linecap="round"/></svg>
    <h3>Forex Market</h3>
    <p>We provide marketing, consumer and business insights through the use of market research.</p>
  </div>
</section>

<section class="strategy">
  <h2 class="abs title">Our Strategy<span class="bar"></span></h2>
  <p class="abs lead">Tradlo.example works with both day as well as intraday traders. We only hold a maximum of one position at any given point in time. Once we’ve placed an order we do not move SL or TP targets.</p>
  <div class="abs box"><p>We follow naked forex trading techniques including price action, immediate trend and personalized mathematical formulas. Our success stems from our strict enforcement of discipline, patience, attitude, economics and timing to help our traders maximize their gains from forex trading. At Tradlo, we trade GBP/USD, EUR/USD, AUD/USD, USD/CHF and USD/JPY pairs only and target anywhere between 25-50 pips a day with a risk:reward ratio of at least 2:1.</p></div>
</section>

<section class="why">
  <div class="abs why-visual" role="img" aria-label="Desktop, laptop and tablet screens showing the site"></div>
  <h2 class="abs">Why Us?</h2>
  <span class="bar"></span>
  <p class="abs lead">Put simply, because we’re different! We are a ‘Never before Seen’ forex trading company that is focused on guiding, mentoring and assisting traders in every possible manner!</p>
  <ul class="abs checks">
    <li><svg width="20" height="20" viewBox="0 0 20 20"><rect width="20" height="20" rx="3" fill="#333"/><path d="M5 10l3.5 3.5L15 7" fill="none" stroke="#fff" stroke-width="2.4"/></svg>We offer speedy, consistent, accurate and desired results.</li>
    <li><svg width="20" height="20" viewBox="0 0 20 20"><rect width="20" height="20" rx="3" fill="#333"/><path d="M5 10l3.5 3.5L15 7" fill="none" stroke="#fff" stroke-width="2.4"/></svg>We’re a highly dependable and trusted forex trading platform.</li>
    <li><svg width="20" height="20" viewBox="0 0 20 20"><rect width="20" height="20" rx="3" fill="#333"/><path d="M5 10l3.5 3.5L15 7" fill="none" stroke="#fff" stroke-width="2.4"/></svg>Our motto is to ‘Reshape Your Path’ and also to ensure that you earn profits</li>
    <li><svg width="20" height="20" viewBox="0 0 20 20"><rect width="20" height="20" rx="3" fill="#333"/><path d="M5 10l3.5 3.5L15 7" fill="none" stroke="#fff" stroke-width="2.4"/></svg>Our objective is to provide global access to trusted forex signals.</li>
    <li><svg width="20" height="20" viewBox="0 0 20 20"><rect width="20" height="20" rx="3" fill="#333"/><path d="M5 10l3.5 3.5L15 7" fill="none" stroke="#fff" stroke-width="2.4"/></svg>Our services are highly affordable.</li>
    <li><svg width="20" height="20" viewBox="0 0 20 20"><rect width="20" height="20" rx="3" fill="#333"/><path d="M5 10l3.5 3.5L15 7" fill="none" stroke="#fff" stroke-width="2.4"/></svg>We offer High Probable forex strategies with high rewards.</li>
  </ul>
</section>

<section class="faq">
  <h2 class="abs title">Our FAQ’S<span class="bar"></span></h2>
  <div class="abs q open" style="top:146px">What is your trading philosophy and style?<svg width="12" height="12" viewBox="0 0 12 12"><path d="M2 2l4 4-4 4M6 2l4 4-4 4" fill="none" stroke="#fff" stroke-width="1.5"/></svg></div>
  <div class="abs q" style="top:212px">How many signals do you send a month?<svg width="12" height="12" viewBox="0 0 12 12"><path d="M2 2l4 4-4 4M6 2l4 4-4 4" fill="none" stroke="#f07c22" stroke-width="1.5"/></svg></div>
  <div class="abs q" style="top:270px">How many pips can I make per month?<svg width="12" height="12" viewBox="0 0 12 12"><path d="M2 2l4 4-4 4M6 2l4 4-4 4" fill="none" stroke="#f07c22" stroke-width="1.5"/></svg></div>
  <div class="abs q" style="top:328px">Can I follow your signals and have a full time job?<svg width="12" height="12" viewBox="0 0 12 12"><path d="M2 2l4 4-4 4M6 2l4 4-4 4" fill="none" stroke="#f07c22" stroke-width="1.5"/></svg></div>
  <div class="abs answer">
    <h3>Answers to your questions:</h3>
    <ul>
      <li><span></span>Our success stems from our strict enforcement of discipline.</li>
      <li><span></span>Help our traders maximize their gains from forex trading.</li>
    </ul>
    <p>We follow naked forex trading techniques including price action, immediate trend and personalized mathematical formulas.</p>
  </div>
</section>

<section class="investors">
  <h2 class="abs title">Investors And Retirees</h2>
  <p class="abs lead">If you are someone that has been tricked before or have lost your savings to investment companies and would like to know how you can take care of your own investment, then we are here to help you. We will show you how to trade your own money so you can control your own investment.</p>
  <p class="abs quote">“We will get you through the steps towards your goal as quickly as possible.”</p>
</section>

<section class="contact">
  <h2 class="abs">Contact Us</h2>
  <div class="abs info" style="top:139px"><span class="ico solid"><svg width="18" height="14" viewBox="0 0 16 12"><rect x="1" y="1" width="14" height="10" fill="none" stroke="#fff" stroke-width="1.6"/><path d="M1 1l7 6 7-6" fill="none" stroke="#fff" stroke-width="1.6"/></svg></span>info@tradlo.example</div>
  <div class="abs info" style="top:219px"><span class="ico solid"><svg width="16" height="20" viewBox="0 0 16 20"><path d="M8 0a7 7 0 0 0-7 7c0 5 7 13 7 13s7-8 7-13a7 7 0 0 0-7-7z" fill="#fff"/><circle cx="8" cy="7" r="2.6" fill="#f07c22"/></svg></span><span>48 Harbor Ln.<br>Westfield, MI 48000</span></div>
  <div class="abs info" style="top:293px"><span class="ico"><svg width="18" height="18" viewBox="0 0 24 24"><path d="M6.6 10.8a15 15 0 0 0 6.6 6.6l2.2-2.2c.3-.3.7-.4 1-.2 1.1.4 2.3.6 3.6.6.6 0 1 .4 1 1V20c0 .6-.4 1-1 1C10.6 21 3 13.4 3 4c0-.6.4-1 1-1h3.5c.6 0 1 .4 1 1 0 1.3.2 2.5.6 3.6.1.3 0 .7-.2 1z" fill="#f07c22"/></svg></span>180 555 0142</div>
  <p class="abs form-title">Fill out the form below, and we’ll contact you shortly.</p>
  <div class="abs field" style="left:485px;top:105px">First Name</div>
  <div class="abs field" style="left:811px;top:105px">Last Name</div>
  <div class="abs field" style="left:485px;top:158px">Phone Number</div>
  <div class="abs field" style="left:811px;top:158px">E-Mail Address</div>
  <div class="abs field msg" style="left:485px;top:212px">Message</div>
  <a class="abs btn-fill">Send Now</a>
</section>

<footer class="site-footer">
  <p class="abs">Copyright © 2017 Tradlo. All rights reserved</p>
  <div class="abs foot-social"><span></span><span></span><span></span></div>
</footer>

</body>
</html>
```